Adelaide based cleaning and remediation business needs a website design

We are launching a new company with no clients as yet so we don't have the benefit of Plimora Reviews to build confidence. We can use our  past work history with other employers in the industry to give some credibility. Happy to use any colour scheme as long as it look interesting when people click on the site it gets there attention. enquiry . I have supplied a mock up the important information and various photos as they tell a lot of the story.

```html
<!DOCTYPE html>
<html lang="en">
<head>
<meta charset="utf-8">
<title>Marlowe Services Pty Ltd</title>
<link href="https://fonts.googleapis.com/css2?family=Poppins:wght@400;500;600;700&family=Open+Sans:wght@400;600&display=swap" rel="stylesheet">
<style>
:root{
  --pink:#d4175f;
  --blue:#5b9fe6;
  --beige:#e8e6d5;
  --beige-soft:#ecebe0;
  --ink:#1f1f1f;
  --text:#444;
  --footer:#1b1b1b;
  --badge:#f2f2ee;
  --grad:linear-gradient(90deg,#d4175f 0%,#b55aa0 55%,#5b9fe6 100%);
}
*{margin:0;padding:0;box-sizing:border-box}
html,body{width:1200px;height:4040px;overflow:hidden;background:#fff}
body{position:relative;font-family:"Open Sans",sans-serif;color:var(--text)}
.abs{position:absolute}
h1,h2,h3,.heading{font-family:"Poppins",sans-serif;color:var(--ink)}
.accent{color:var(--pink)}
.btn{position:absolute;display:flex;align-items:center;justify-content:center;border-radius:30px;background:var(--grad);color:#fff;font-family:"Poppins",sans-serif;font-weight:600;font-size:12px;text-transform:uppercase;letter-spacing:.2px}
/* hero */
.hero-bg{left:0;top:0;width:1200px;height:560px}
.brand{left:99px;top:44px;display:flex;align-items:center;gap:10px;font-family:"Poppins",sans-serif;font-weight:600;font-size:17px;color:var(--ink)}
.brand-mark{width:22px;height:22px;background:var(--ink)}
.nav{left:508px;top:34px;display:flex;gap:34px;font-family:"Poppins",sans-serif;font-size:13px;color:#333}
.nav .active{color:var(--pink)}
.hero-photo{left:706px;top:47px;width:392px;height:541px;border-radius:48% 48% 40% 40%;background:linear-gradient(170deg,#5b8fd6 0%,#4a78c0 45%,#7ed23a 80%,#5aa02a 100%);opacity:.85}
.hero-title{left:99px;top:190px;font-size:56px;font-weight:600;letter-spacing:-.5px}
.hero-sub{left:101px;top:266px;font-family:"Open Sans",sans-serif;font-size:33px;color:var(--ink)}
/* services */
.section-title{width:1200px;left:0;text-align:center;font-size:40px;font-weight:600;line-height:47px}
.card{width:340px;text-align:center}
.card-media{position:relative;width:295px;height:295px;margin:0 auto;border-radius:50% 0 50% 50%}
.card-media .photo{position:absolute;left:14px;top:0;width:281px;height:281px;border-radius:50% 0 50% 50%}
.card h3{margin-top:36px;font-size:20px;font-weight:600}
.card p{margin:14px auto 0;width:280px;font-size:15.5px;line-height:24px}
.list{list-style:none;text-align:left;margin-top:14px;padding-left:0}
.list li{position:relative;padding-left:28px;font-size:15.5px;line-height:24px;margin-bottom:9px}
.list li::before{content:"";position:absolute;left:0;top:6px;width:14px;height:12px;border-radius:8px 0 8px 0;background:var(--dot)}
/* about */
.about-title{left:624px;top:1785px;font-size:40px;font-weight:600;line-height:49px}
.body-text{font-size:14.5px;line-height:26.5px}
.round-photo{border-radius:50%}
/* testimonial */
.quote-card{left:169px;top:3114px;width:862px;height:190px;border-radius:12px;background:linear-gradient(100deg,var(--beige) 0%,var(--beige) 55%,#ecb3c6 80%,#a6c4e3 100%)}
.quote-card p{position:absolute;left:53px;top:44px;width:740px;font-size:15px;line-height:26px}
.quote-card strong{color:var(--ink);font-weight:600}
.quote-name{position:absolute;left:53px;top:136px;font-family:"Poppins",sans-serif;font-weight:600;font-size:15px;color:var(--ink)}
/* contact form */
.form{left:264px;top:3577px;width:673px;height:79px;border-radius:40px;background:var(--beige-soft)}
.form span{position:absolute;left:42px;top:30px;font-family:"Poppins",sans-serif;font-size:14px;color:#333}
/* footer */
.footer{left:0;top:3762px;width:1200px;height:278px;background:var(--footer)}
.badge{left:121px;top:3820px;width:199px;height:74px;background:var(--badge);border-radius:4px}
.f-col{font-family:"Poppins",sans-serif;color:#eee;font-size:11.5px;line-height:22px}
.f-col h4{color:var(--pink);font-size:14px;font-weight:600;margin-bottom:6px;text-transform:uppercase}
.f-col b{font-weight:600;color:#fff}
.copyright{left:0;top:3993px;width:1200px;text-align:center;font-family:"Poppins",sans-serif;font-size:11.5px;color:#ddd}
</style>
</head>
<body>

<!-- Hero -->
<svg class="abs hero-bg" viewBox="0 0 1200 560" aria-hidden="true">
  <defs>
    <linearGradient id="heroGrad" x1="0" y1="0" x2="1" y2="0">
      <stop offset="0" stop-color="#e6e2cc"/>
      <stop offset=".55" stop-color="#e7e2cf"/>
      <stop offset=".75" stop-color="#e9a8bf"/>
      <stop offset="1" stop-color="#a9a6d6"/>
    </linearGradient>
  </defs>
  <path d="M0 0H1200V430C1120 500 980 540 840 530C660 515 520 470 380 500C260 525 120 520 60 480C30 462 12 448 0 432Z" fill="url(#heroGrad)"/>
</svg>

<div class="abs brand"><span class="brand-mark"></span>Marlowe</div>
<nav class="abs nav">
  <span class="active">Home</span><span>Services</span><span>About</span><span>Pricing</span><span>FAQs</span><span>Contact</span>
</nav>
<div class="btn" style="left:966px;top:22px;width:135px;height:45px">Book Now</div>

<div class="abs hero-photo" role="img" aria-label="Cleaner in blue protective suit and respirator holding a green basket of waste"></div>

<h1 class="abs hero-title">Marlowe Services Pty Ltd</h1>
<div class="abs hero-sub">#1 Dirty Job Cleaners</div>
<div class="btn" style="left:102px;top:342px;width:240px;height:44px">Get Pricing &amp; Book Online</div>

<!-- Services -->
<h2 class="abs section-title" style="top:643px"><span class="accent">We Do The Stuff</span> Nobody<br>wants to do</h2>

<div class="abs card" style="left:76px;top:800px">
  <div class="card-media" style="background:var(--pink)">
    <div class="photo" role="img" aria-label="Pigeons perched on a stained ledge" style="background:linear-gradient(160deg,#c9d2dc,#8f8a80 60%,#6a5a48)"></div>
  </div>
  <h3>Pigeon Waste</h3>
  <p>Can cause damage to buildings and spread disease, mites and bacteria, triggering alarms and damaging the reputation of businesses.</p>
  <ul class="list" style="--dot:var(--pink);margin-left:22px;width:300px">
    <li>The pigeon faeces is carefully removed by our trained operatives, who also dispose of it in an environmentally friendly way.</li>
    <li>Next, in order to remove stains and ensure safety, we use eco-friendly chemicals to clean and disinfect the impacted areas.</li>
    <li>We advise adding anti-nesting spikes as an option.</li>
  </ul>
</div>

<div class="abs card" style="left:429px;top:800px">
  <div class="card-media" style="background:var(--blue)">
    <div class="photo" role="img" aria-label="Cluttered fire damaged room full of belongings" style="background:linear-gradient(160deg,#8a6a4a,#b04a3a 45%,#5a4a3a)"></div>
  </div>
  <h3>Fire Damage Clean Outs</h3>
  <ul class="list" style="--dot:var(--blue);margin-left:48px;width:270px">
    <li>Removal of debris</li>
    <li>On site cleaning of contents</li>
    <li>Cleaning of carpets and upholstered items</li>
    <li>Catalogue all contents for packing and storage</li>
    <li>Pressure cleaning of contaminated surfaces</li>
  </ul>
</div>

<div class="abs card" style="left:782px;top:800px">
  <div class="card-media" style="background:var(--beige)">
    <div class="photo" role="img" aria-label="Shed filled with burnt and scattered estate debris" style="background:linear-gradient(160deg,#9a9a94,#5a544c 50%,#3a3a40)"></div>
  </div>
  <h3>Squlaor Estate Clean ups</h3>
  <p>Marlowe Services is a hoarding clean up firm that approaches clutter removal personally. We always operate with compassion, prioritising the individuals involved over the cleaning procedure, and we understand the psychology of a person's hoarding attitude.</p>
  <ul class="list" style="--dot:#d6d4bd;margin-left:22px;width:320px">
    <li>Clutter Removal</li>
    <li>Search And Recovery Of Items: paperwork, collectibles, valuables, etc.</li>
    <li>Packing And Storing</li>
    <li>Deep Cleaning</li>
    <li>Odor Removal</li>
  </ul>
</div>

<!-- About -->
<svg class="abs" style="left:0;top:1600px" width="1200" height="720" viewBox="0 0 1200 720" aria-hidden="true">
  <defs>
    <linearGradient id="aboutGrad" x1="0" y1="0" x2="1" y2="0">
      <stop offset="0" stop-color="#a9c2db"/>
      <stop offset=".3" stop-color="#eaa5bd"/>
      <stop offset=".5" stop-color="#e8e5d3"/>
      <stop offset="1" stop-color="#e8e6d5"/>
    </linearGradient>
  </defs>
  <path d="M0 170C120 60 260 20 420 60C600 105 760 120 900 60C1020 10 1130 20 1200 90V620C1130 640 1030 720 880 700C700 675 560 620 420 640C260 662 120 670 0 640Z" fill="url(#aboutGrad)"/>
</svg>
<div class="abs round-photo" style="left:99px;top:1754px;width:410px;height:410px;border:6px solid #e6e2cc;background:linear-gradient(150deg,#c8a870,#e8d9b0 35%,#3a3836 65%,#222)" role="img" aria-label="Worker in white protective suit clearing debris from a gutter on a roof"></div>
<h2 class="abs about-title"><span class="accent">About</span><br>Marlowe Services</h2>
<p class="abs body-text" style="left:624px;top:1906px;width:480px">Adelaide-based Marlowe Services is a family-run organisation. We have been in operation for more than two decades. We've gained some knowledge about cleaning and squalor removal services throughout the years. As a small South Australian company, we base everything on responsibility honesty and fairness .We are aware of the confi-dence you put in us when you seek our help.</p>
<div class="btn" style="left:624px;top:2095px;width:134px;height:43px">Learn More</div>

<!-- Plans -->
<h2 class="abs" style="left:99px;top:2470px;font-size:40px;font-weight:600;line-height:47px"><span class="accent">Plans That Scale</span><br>With You</h2>
<p class="abs body-text" style="left:99px;top:2593px;width:480px">Prices provided in terms of the number of hoursand service required or as a fixed quotationaccording to the quantity of clutter, pigeonfaeces, and mould disposal expenses; however,hoarding cleaning can be different as this mayrequire sorting and can require moreorganisation.</p>
<div class="btn" style="left:99px;top:2761px;width:134px;height:43px">Learn More</div>
<div class="abs round-photo" style="left:692px;top:2408px;width:408px;height:408px;border:6px solid var(--blue);background:linear-gradient(160deg,#e4a0b0,#5a4438 40%,#2a2624 70%,#8a6a50)" role="img" aria-label="Fire damaged kitchen with burnt stove and exposed ceiling insulation"></div>

<!-- Testimonials -->
<h2 class="abs section-title" style="top:2966px"><span class="accent">Only the best</span> service<br>for our customers</h2>
<svg class="abs" style="left:84px;top:3198px" width="34" height="24" viewBox="0 0 34 24" aria-label="Previous"><path d="M32 12H3M12 3L3 12L12 21" fill="none" stroke="#222" stroke-width="2.4"/></svg>
<div class="abs quote-card">
  <p>Dean and his team arrived the next morning to clean up a rental property my husband and I own which and had been trashed by the tenants. He was the only contractor to return my call. <strong>They did an amazing</strong> job and also deodorised the house for no extra charge.</p>
  <div class="quote-name">Helena Marsh, Satisfied customer</div>
</div>
<svg class="abs" style="left:1082px;top:3198px" width="34" height="24" viewBox="0 0 34 24" aria-label="Next"><path d="M2 12H31M22 3L31 12L22 21" fill="none" stroke="#222" stroke-width="2.4"/></svg>

<!-- Enquiry -->
<h2 class="abs section-title" style="top:3392px"><span class="accent">Send a text to Marlowe Services</span><br>Please enter your mobile number or<br>email and message</h2>
<div class="abs form"><span>Email Address or Mobile no.</span></div>
<div class="btn" style="left:783px;top:3593px;width:133px;height:47px">Submit Now</div>

<!-- Footer -->
<div class="abs footer"></div>
<div class="abs badge" role="img" aria-label="Industry certification badge"></div>
<div class="btn" style="left:104px;top:3913px;width:238px;height:44px">Get Pricing &amp; Book Online</div>

<div class="abs f-col" style="left:466px;top:3812px">
  <h4>Quick Links</h4>
  Home<br>Services<br>About<br>Pricing<br>FAQs
</div>
<div class="abs f-col" style="left:667px;top:3812px">
  <h4>Other Links</h4>
  Contact Us<br>Privacy Policy<br>Book Now<br>Contact Us<br>Order confirmation
</div>
<div class="abs f-col" style="left:893px;top:3812px;width:240px">
  <h4>Contact</h4>
  <b>Marlowe, 12 Keller Street Norwood SA 5067</b><br>
  <b>Call:</b> Dean or Priya 0400 555 018<br>
  <b>Email:</b> admin@marloweservices.com
</div>
<div class="abs copyright">2025 Marlowe. All Rights Reserved.</div>

</body>
</html>
```